Ridge Lass Crew (Flyer)

I want a flyer to advertise my service.
Details below, and logo's to use are attached.

A girls only after school program, 11-14yrs, as OSHC is no longer avail, dedicated to coaching & mentoring our girls into strong, independent young women.

The Brainchild of Rebecca Folwin, Ridge Lass Crew was created to address the growing demand for after school/school holiday supervision for kids moving from primary into high school, when OSHC ceases to exist.
With over 12 years experience mentoring and coaching young women in the corporate world, Bec decided to leave her role as a Director with Tarrant Trust, and follow her passion.
Bec, along with her sister Lorraine, who has over 10 years experience in local communities as a Youth Worker, and is also a qualified Enrolled Nurse, embarked on building a program designed to keep parents happy (by knowing their girls are safe) and dedicated to coaching and mentoring our girls into strong, independent young women.
Open every afternoon and during school holidays, we look to offer;
- Daily meditation
- Healthy snacks
- Dedicated homework time
- Organised group activity, led by qualified instructors (yoga, fitness class, soccer etc)
- Regular guests speakers, addressing issues/concerns for young people today
- SOCIAL MEDIA FREE ZONE

Located 87 Pelham Pde, Ashgrove Vale (across from Crestmoor Day Clinic)
Open 3-6pm Monday to Friday

Facebook page: http://fb.example/ridgelasscrew
Email: info@ridgelasscrew.example.au
Mobile: 0455817396

Target Market(s)

Parents of teenage girls, teenage girls 11-14 years

Industry/Entity Type

School

Font styles to use
Sans Serif

Colors
b768aa
e667a6

Requirements
Must have
• What progam is - see brief
• Who runs it
Should not have
• Not be too busy, not overly mature images

```html
<!DOCTYPE html>
<html lang="en">
<head>
<meta charset="utf-8">
<title>Ridge Lass Crew – After School Program Flyer</title>
<link rel="stylesheet" href="https://fonts.googleapis.com/css2?family=Cinzel:wght@600;700&family=Open+Sans:wght@400;600;700&family=Roboto+Condensed:wght@400&family=Cabin:wght@500&display=swap">
<style>
  :root {
    --violet: #bb5ef2;
    --magenta: #f15fe0;
    --logo-pink: #ee3fc7;
    --ink: #262326;
    --ink-soft: #4b3f56;
    --navy: #2f3552;
    --white: #ffffff;
    --photo-light: #eeece8;
    --photo-mid: #d6d3cd;
    --photo-dark: #b9b3ac;
  }
  * { margin: 0; padding: 0; box-sizing: border-box; }
  html, body { width: 934px; height: 1200px; overflow: hidden; background: var(--white); }
  .flyer { position: relative; width: 934px; height: 1200px; overflow: hidden; font-family: "Open Sans", sans-serif; color: var(--ink); }

  .top-band { position: absolute; left: 0; top: 0; width: 934px; height: 144px; background: var(--violet); }
  .hero-photo {
    position: absolute; left: 0; top: 144px; width: 934px; height: 484px;
    background: radial-gradient(ellipse 340px 300px at 480px 250px, var(--photo-light) 0%, var(--photo-mid) 70%, var(--photo-dark) 100%);
  }

  .logo-card {
    position: absolute; left: 627px; top: 44px; width: 291px; height: 324px;
    background: var(--white); display: flex; align-items: center; justify-content: center;
  }
  .logo-card .brand-name {
    font-family: "Cinzel", serif; font-weight: 700; color: var(--logo-pink);
    font-size: 40px; line-height: 1.15; text-align: center;
  }

  .headline { position: absolute; left: 0; top: 248px; width: 408px; height: 184px; font-family: "Cinzel", serif; font-weight: 700; color: var(--ink); font-size: 31px; }
  .headline span {
    position: absolute; right: 0; background: var(--magenta);
    padding-right: 8px; display: flex; align-items: center; justify-content: flex-end; white-space: nowrap;
  }
  .headline .line-1 { top: 0; left: 8px; height: 52px; }
  .headline .line-2 { top: 56px; left: 44px; height: 60px; }
  .headline .line-3 { top: 122px; left: 78px; height: 60px; }
  .headline-note { position: absolute; left: 112px; top: 434px; font-weight: 700; font-size: 17px; color: var(--ink); }

  .info-band {
    position: absolute; left: 0; top: 628px; width: 934px; height: 180px; background: var(--violet);
    text-align: center; font-family: "Cinzel", serif; color: var(--ink);
  }
  .info-band .founder { position: absolute; left: 0; right: 0; top: 20px; font-size: 21px; font-weight: 700; }
  .info-band .program-name { position: absolute; left: 0; right: 0; top: 52px; font-size: 36px; font-weight: 600; letter-spacing: 1px; }
  .info-band .availability { position: absolute; left: 0; right: 0; top: 104px; font-family: "Cabin", sans-serif; font-weight: 500; font-size: 25px; color: var(--ink-soft); }
  .info-band .hours { position: absolute; left: 0; right: 0; top: 142px; font-size: 21px; font-weight: 600; }

  .section-heading {
    position: absolute; font-weight: 700; font-size: 24px; color: var(--navy); letter-spacing: 0.5px;
    padding-left: 30px;
  }
  .section-heading::before {
    content: ""; position: absolute; left: 0; top: 2px; width: 4px; height: 30px; background: var(--violet);
  }
  .about-heading { left: 50px; top: 836px; }
  .offer-heading { left: 604px; top: 830px; }
  .about-text { position: absolute; left: 42px; top: 898px; width: 520px; font-size: 18px; line-height: 30px; hyphens: auto; }

  .offer-list { position: absolute; left: 606px; top: 886px; list-style: none; font-size: 19px; line-height: 30px; }
  .offer-list li { position: relative; padding-left: 26px; margin-bottom: 1px; }
  .offer-list li::before {
    content: ""; position: absolute; left: 0; top: 10px; width: 8px; height: 8px; border-radius: 50%; background: var(--magenta);
  }
  .offer-list .detail { display: block; padding-left: 10px; }

  .footer-band { position: absolute; left: 0; top: 1112px; width: 934px; height: 88px; background: var(--violet); color: var(--white); }
  .address { position: absolute; left: 96px; top: 24px; font-family: "Roboto Condensed", sans-serif; font-size: 19px; }
  .address small { display: block; font-size: 11px; margin-top: 4px; padding-left: 10px; }
  .pin-icon { position: absolute; left: 62px; top: 22px; }
  .phone { position: absolute; left: 440px; top: 24px; font-family: "Roboto Condensed", sans-serif; font-size: 20px; }
  .phone-icon { position: absolute; left: 400px; top: 22px; }
  .contact { position: absolute; right: 28px; top: 4px; text-align: right; font-weight: 700; font-size: 16px; line-height: 28px; }
  .contact .mail-label { padding-right: 26px; position: relative; }
  .contact .mail-label svg { position: absolute; right: 0; top: 4px; }
  .contact .social-link { padding-right: 24px; position: relative; }
  .contact .social-link::after {
    content: ""; position: absolute; right: 0; top: 6px; width: 15px; height: 15px; background: var(--white);
  }
</style>
</head>
<body>
<main class="flyer">
  <div class="top-band"></div>
  <div class="hero-photo" role="img" aria-label="Photo of a girl wearing a white program t-shirt with the program's name printed on it"></div>

  <div class="logo-card">
    <p class="brand-name">Ridge Lass<br>Crew</p>
  </div>

  <h1 class="headline">
    <span class="line-1">A Girls Only After</span>
    <span class="line-2">School Program</span>
    <span class="line-3">For 11-14yrs</span>
  </h1>
  <p class="headline-note">as OSHC is no longer available</p>

  <section class="info-band">
    <p class="founder">The Brainchild of Rebecca Folwin</p>
    <h2 class="program-name">Ridge Lass Crew</h2>
    <p class="availability">Open every afternoon &amp; during school holidays</p>
    <p class="hours">3-6pm Monday to Friday</p>
  </section>

  <h3 class="section-heading about-heading">WHO WE ARE</h3>
  <p class="about-text">The Brainchild of Rebecca Folwin, Ridge Lass Crew was created to address the growing demand for after school/school holiday supervision for kids moving from primary into high school, when OSHC ceases to exist.</p>

  <h3 class="section-heading offer-heading">WHAT WE OFFER</h3>
  <ul class="offer-list">
    <li>Daily meditation</li>
    <li>Healthy snacks</li>
    <li>Organised group activity,<span class="detail">(yoga, fitness class, soccer etc.)</span></li>
    <li>Regular guests speakers</li>
    <li>Dedicated homework time</li>
    <li>Social media free zone</li>
  </ul>

  <footer class="footer-band">
    <svg class="pin-icon" width="20" height="26" viewBox="0 0 20 26" fill="none" stroke="#ffffff" stroke-width="1.6">
      <path d="M10 25 C10 25 2 15 2 9.5 A8 8 0 0 1 18 9.5 C18 15 10 25 10 25 Z"/>
      <circle cx="10" cy="9.5" r="3"/>
    </svg>
    <p class="address">87 Pelham Pde, Ashgrove Vale<small>(across from Crestmoor Day Clinic)</small></p>

    <svg class="phone-icon" width="26" height="24" viewBox="0 0 26 24" fill="none" stroke="#ffffff" stroke-width="1.6" stroke-linecap="round">
      <path d="M4 3 L8 3 L10 8 L7.5 10 C9 13.5 11 15.5 14 17 L16 14.5 L21 16.5 L21 20.5 C12 21 3.5 12 4 3 Z"/>
      <path d="M15 3 A7 7 0 0 1 22 10"/>
      <path d="M15 7 A3 3 0 0 1 18 10"/>
    </svg>
    <p class="phone">Call: 0455817396</p>

    <div class="contact">
      <p class="mail-label">e-Mail us
        <svg width="20" height="16" viewBox="0 0 20 16" fill="none" stroke="#ffffff" stroke-width="1.4">
          <rect x="1" y="1" width="18" height="14"/>
          <path d="M1 1 L10 9 L19 1"/>
        </svg>
      </p>
      <p>info@ridgelasscrew.example.au</p>
      <p class="social-link">http://fb.example/ridgelasscrew</p>
    </div>
  </footer>
</main>
</body>
</html>
```